The Vantor Codex Book Cover

"The Vantor Codex" is a book I wrote with the slogan "Unlock Performance, Spark Engagement: Master the Art of Building Winning Cultures in Today's Hybrid World". The book is designed around a methodology that's mine and that I attached. I would love to see the graphic of the methodology integrated in the design in a very subtle way. Use colors from the model but the book cover should be catchy, modern and engaging to the eye.
Overall the book is about three key elements towards success:
- (Self) Directions (purpose)
- Human experience (people and psychological safety)
- Maximize engagement
The methodology is a FLOW so flow is something that could be incorporated as well in the concept.
Low design quality
Managers and Teams

```html
<!DOCTYPE html>
<html lang="en">
<head>
<meta charset="UTF-8">
<title>The Vantor Codex — Book Cover</title>
<link href="https://fonts.googleapis.com/css2?family=Montserrat:wght@400;800&family=Cormorant+Garamond:ital,wght@1,400&family=Cinzel:wght@400&family=Bebas+Neue&display=swap" rel="stylesheet">
<style>
  :root {
    --cover-blue: #1c3f8f;
    --mist-teal: #b9d4d3;
    --slate-ink: #2d4650;
    --paper: #ffffff;
    --title-white: #f1f1f1;
    --author-ink: #1d1d1d;
  }
  html, body {
    margin: 0;
    padding: 0;
    width: 934px;
    height: 1200px;
    overflow: hidden;
    background: var(--paper);
  }
  .cover {
    position: relative;
    width: 934px;
    height: 1200px;
    overflow: hidden;
    background: var(--paper);
  }
  .cover-photo {
    position: absolute;
    inset: 0 0 auto 0;
    height: 612px;
    background:
      radial-gradient(ellipse at 20% 70%, rgba(255,255,255,0.85), rgba(255,255,255,0) 45%),
      radial-gradient(ellipse at 55% 40%, #c99a82 0%, rgba(201,154,130,0) 35%),
      radial-gradient(ellipse at 88% 35%, #5c5b5e 0%, rgba(92,91,94,0) 40%),
      linear-gradient(160deg, #d9dee6 0%, #b8c3d3 40%, #c7d0dc 70%, #8e9cb0 100%);
  }
  .title-band {
    position: absolute;
    top: 612px;
    left: 0;
    width: 934px;
    height: 322px;
    background: var(--cover-blue);
  }
  .title-the {
    position: absolute;
    top: 572px;
    left: 0;
    width: 934px;
    text-align: center;
    font-family: "Cormorant Garamond", serif;
    font-style: italic;
    font-size: 72px;
    line-height: 1;
    color: var(--title-white);
    letter-spacing: -1px;
  }
  .title-main {
    position: absolute;
    top: 636px;
    left: 0;
    width: 934px;
    text-align: center;
    font-family: "Montserrat", sans-serif;
    font-weight: 800;
    font-size: 142px;
    line-height: 1;
    color: var(--title-white);
    letter-spacing: -2px;
  }
  .title-sub {
    position: absolute;
    top: 790px;
    left: 0;
    width: 934px;
    text-align: center;
    font-family: "Cinzel", serif;
    font-size: 68px;
    line-height: 1;
    color: var(--title-white);
    letter-spacing: 0.62em;
    text-indent: 0.62em;
  }
  .slogan-row {
    position: absolute;
    top: 880px;
    left: 0;
    width: 934px;
    height: 72px;
  }
  .slogan-left, .slogan-right {
    position: absolute;
    top: 25px;
    font-family: "Bebas Neue", sans-serif;
    font-size: 19px;
    line-height: 1;
    color: var(--title-white);
    letter-spacing: 0.42em;
  }
  .slogan-left { left: 125px; }
  .slogan-right { left: 515px; top: 27px; }
  .flow-mark {
    position: absolute;
    top: 0;
    left: 405px;
    width: 98px;
    height: 58px;
  }
  .tagline-band {
    position: absolute;
    top: 934px;
    left: 0;
    width: 934px;
    height: 97px;
    background: var(--mist-teal);
  }
  .tagline {
    margin: 0;
    padding-top: 19px;
    text-align: center;
    font-family: "Bebas Neue", sans-serif;
    font-size: 29px;
    line-height: 32px;
    color: var(--slate-ink);
  }
  .author {
    position: absolute;
    top: 1088px;
    left: 0;
    width: 934px;
    text-align: center;
    font-family: "Montserrat", sans-serif;
    font-weight: 400;
    font-size: 54px;
    line-height: 1;
    color: var(--author-ink);
    letter-spacing: 0.36em;
    text-indent: 0.36em;
  }
</style>
</head>
<body>
  <main class="cover">
    <div class="cover-photo" role="img" aria-label="Low-angle photo of a team of colleagues stacking their hands together in the middle"></div>
    <div class="title-band"></div>

    <div class="title-the">THE</div>
    <div class="title-main">VANTOR</div>
    <div class="title-sub">CODEX</div>

    <div class="slogan-row">
      <span class="slogan-left">UNLOCK PERFORMANCE,</span>
      <svg class="flow-mark" viewBox="0 0 98 58" role="img" aria-label="Colourful flow methodology graphic">
        <defs>
          <linearGradient id="flowTones" x1="0" y1="0" x2="1" y2="1">
            <stop offset="0" stop-color="#e97a86"/>
            <stop offset="0.5" stop-color="#7cc3c6"/>
            <stop offset="1" stop-color="#c9d27e"/>
          </linearGradient>
        </defs>
        <circle cx="49" cy="29" r="28" fill="url(#flowTones)"/>
      </svg>
      <span class="slogan-right">SPARK ENGAGEMENT:</span>
    </div>

    <section class="tagline-band">
      <p class="tagline">MASTER THE ART OF BUILDING WINNING<br>CULTURES IN TODAY'S HYBRID WORLD</p>
    </section>

    <div class="author">LARS EVERDINGEN</div>
  </main>
</body>
</html>
```